lantern pathway for children needs a website designer

We need a website designer for our new extension to our company known as 'lantern pathway' providing shadow support services to children based in Singapore. We are a sister branch of a private clinic 'Bright horizons' providing speech language, occupational, and educational therapy to children.

We would like to use our own photos. So the selected design should have a frame with pictures to give us an idea but we will replace them with our own. We will be needing help with inputting information and changing information throughout.

We would like to see designs that are simple, and professional. We have a logo (see attached). The result should convey professionalism in shadow support, fostering independent thinking and moving students towards self-learning.

Target Market(s)

Teachers, psychologists, parents

Industry/Entity Type

Clinic

Requirements
Should not have
• too distracting colours

```html
<!DOCTYPE html>
<html lang="en">
<head>
<meta charset="utf-8">
<title>Lantern Pathway – Shadow Support</title>
<link rel="stylesheet" href="https://fonts.googleapis.com/css2?family=Arimo:wght@400;700&family=Ubuntu:wght@400;500&family=Michroma&display=swap">
<style>
:root{
  --red:#8e0d12;
  --red-dark:#6e0a0e;
  --red-band:#a51c1f;
  --red-footer:#9a1518;
  --grey-bg:#efefef;
  --grey-panel:#dcdcdc;
  --text:#666;
  --text-dark:#333;
  --white:#fff;
  --gold:#e0ae1a;
  --copy-bar:#3a3a3a;
}
*{box-sizing:border-box;margin:0;padding:0}
html,body{width:1200px;height:2560px;overflow:hidden}
body{position:relative;background:var(--grey-bg);font-family:"Arimo",Arial,sans-serif;color:var(--text)}
h1,h2,h3,h4{font-weight:400}
.abs{position:absolute}

.top-line{left:0;top:0;width:1200px;height:9px;background:var(--red-dark)}
.page-glow{left:0;top:9px;width:1200px;height:890px;background:linear-gradient(180deg,#f7f7f7,#ececec 60%,#f2f2f2)}

/* header */
.nav-bar{left:43px;top:51px;width:1102px;height:48px;border-radius:6px;background:linear-gradient(180deg,#a3171c,#6e0a0e)}
.nav-list{right:24px;top:0;height:48px;display:flex;gap:50px;align-items:center;list-style:none}
.nav-list li{color:var(--white);font-size:16px;letter-spacing:1px}
.brand{left:55px;top:31px;width:204px;height:89px;border-radius:6px;background:linear-gradient(180deg,#ffffff,#dadada);box-shadow:0 3px 6px rgba(0,0,0,.3);display:flex;align-items:center;justify-content:center}
.brand-name{font-family:"Ubuntu",sans-serif;font-weight:500;font-size:25px;color:var(--red);text-align:center;line-height:1.05}

/* hero */
.hero{left:44px;top:145px;width:1110px;height:384px;border-radius:6px;background:linear-gradient(180deg,#e6e6e6,#d3d3d3);box-shadow:0 0 0 3px #d0d0d0 inset}
.hero-photo{left:7px;top:7px}
.hero-title{left:502px;top:72px;font-family:"Michroma",sans-serif;font-size:18px;letter-spacing:1.5px;color:var(--red-dark);white-space:nowrap}
.hero-title span{color:var(--red)}
.hero-copy{left:502px;top:106px;width:540px;font-size:15.5px;line-height:27px;letter-spacing:.6px;text-align:justify;color:#777}
.btn{display:flex;align-items:center;justify-content:center;color:var(--white);background:linear-gradient(180deg,#a3171c,#6e0a0e);border-radius:3px;letter-spacing:1px}
.hero-btn{left:506px;top:234px;width:273px;height:48px;font-size:22px}
.hero-dots{left:1022px;top:356px;display:flex;gap:7px}
.hero-dots i{width:12px;height:12px;border-radius:50%;background:var(--red);border:2px solid #fff;box-shadow:0 0 2px #888}

/* welcome */
.welcome-title{left:0;top:558px;width:1200px;text-align:center;font-size:30px;letter-spacing:1.5px;color:var(--text-dark)}
.welcome-title span{color:var(--red)}
.welcome-rule{left:80px;top:622px;width:1021px;height:1px;background:#c9c9c9}
.welcome-copy{left:154px;top:647px;width:880px;text-align:center;font-size:15.5px;line-height:23px;letter-spacing:.8px;color:#6a6a6a}
.welcome-copy p+p{margin-top:22px}

/* services */
.services-band{left:0;top:900px;width:1200px;height:554px;background-color:#e6e6e6;background-image:radial-gradient(#d3d3d3 1px,transparent 1px);background-size:4px 4px}
.service-card{top:913px;height:418px;border-radius:10px;background:linear-gradient(180deg,#f4f4f4,#cfcfcf);border:6px solid #dedede;box-shadow:0 1px 3px rgba(0,0,0,.25)}
.service-ring{top:825px;width:222px;height:222px;border-radius:50%;background:#f2f2f2;border:3px solid #d8d8d8;display:flex;align-items:center;justify-content:center}
.service-ring svg{border-radius:50%}
.service-title{position:absolute;left:22px;top:152px;font-size:20px;letter-spacing:1px;color:var(--text-dark)}
.service-title span{color:var(--red)}
.service-text{position:absolute;left:22px;top:182px;width:220px;font-size:14.5px;line-height:21px;letter-spacing:.8px;text-align:justify;color:#888}
.service-btn{position:absolute;left:22px;top:325px;width:218px;height:40px;font-size:16px}

/* shadow support band */
.support-band{left:0;top:1454px;width:1200px;height:379px;background:linear-gradient(90deg,#9c1416,#b02427 50%,#9c1416)}
.support-title{left:0;top:1480px;width:1200px;text-align:center;font-family:"Ubuntu",sans-serif;font-size:26px;letter-spacing:1px;color:var(--white)}
.support-rule{left:400px;top:1528px;width:400px;height:1px;background:rgba(255,255,255,.3)}
.support-copy{left:162px;top:1558px;width:422px;font-family:"Ubuntu",sans-serif;font-size:15.5px;line-height:25px;letter-spacing:.3px;color:#f5dede;text-align:justify}
.support-list{left:645px;top:1560px;width:440px;list-style:none;font-family:"Ubuntu",sans-serif;font-size:15.5px;line-height:20px;color:#f5dede}
.support-list li{display:flex;gap:10px;margin-bottom:16px}
.support-list svg{flex:none;margin-top:4px}
.support-goal{left:162px;top:1732px;width:960px;font-family:"Ubuntu",sans-serif;font-size:15.5px;color:#f5dede}
.support-foot{left:162px;top:1799px;width:876px;height:1px;background:rgba(255,255,255,.2)}

/* info */
.info{top:1833px;height:458px;left:0;width:1200px;background:#f3f3f3}
.info-col{top:1874px;font-family:"Ubuntu",sans-serif}
.info-col h3{font-size:20px;color:var(--red);margin-bottom:12px}
.info-col h3 small{font-size:18px;color:var(--text-dark)}
.info-col p{font-size:15px;line-height:25px;color:#6a6a6a;text-align:justify;margin-bottom:20px}
.info-col p.tight{margin-bottom:12px}
.info-btn{position:relative;width:236px;height:50px;font-size:20px;margin-top:8px;font-family:"Arimo",sans-serif}

/* footer */
.footer{left:0;top:2291px;width:1200px;height:235px;background:linear-gradient(180deg,#a1181b,#8a1014)}
.footer-head{top:2332px;font-size:20px;letter-spacing:1.2px;color:var(--white)}
.footer-rule{left:80px;top:2371px;width:1012px;border-top:2px dotted rgba(255,255,255,.6)}
.footer-list{top:2389px;list-style:none;font-size:11px;letter-spacing:.5px;color:var(--white);line-height:20px}
.footer-list li::before{content:"";display:inline-block;width:6px;height:6px;border-radius:50%;background:#fff;margin-right:6px;vertical-align:middle}
.social{left:624px;top:2403px;display:flex;gap:12px}
.social i{width:32px;height:32px;border-radius:50%;background:var(--white)}
.email{left:884px;top:2397px;width:174px;height:37px;border-radius:3px;background:var(--white);font-size:17px;color:#ccc;padding:8px 12px}
.subscribe{left:884px;top:2446px;width:174px;height:39px;border-radius:3px;background:linear-gradient(180deg,#edbe2c,#d29f10);color:var(--white);font-size:13px;letter-spacing:1px;display:flex;align-items:center;justify-content:center}
.copyright{left:0;top:2526px;width:1200px;height:34px;background:var(--copy-bar);color:#ddd;font-size:13px;letter-spacing:.8px;display:flex;align-items:center;justify-content:center}
</style>
</head>
<body>
<div class="abs top-line"></div>
<div class="abs page-glow"></div>

<header>
  <div class="abs nav-bar">
    <ul class="abs nav-list">
      <li>HOME</li><li>ABOUT US</li><li>SERVICES</li><li>NEWS</li><li>REGISTER</li><li>CONTACT US</li>
    </ul>
  </div>
  <div class="abs brand"><span class="brand-name">Lantern<br>Pathway</span></div>
</header>

<section class="abs hero">
  <svg class="abs hero-photo" width="485" height="370" viewBox="0 0 485 370" role="img" aria-label="Photo of a teacher reading with a young pupil in a library">
    <defs>
      <linearGradient id="heroPhotoTone" x1="0" y1="0" x2="1" y2="1">
        <stop offset="0" stop-color="#b79a72"/>
        <stop offset=".5" stop-color="#d9b88e"/>
        <stop offset="1" stop-color="#8fa27a"/>
      </linearGradient>
    </defs>
    <path d="M0 0H455Q395 185 455 370H0Z" fill="url(#heroPhotoTone)"/>
    <path d="M455 0Q395 185 455 370" fill="none" stroke="#7e0a0e" stroke-width="6"/>
  </svg>
  <h1 class="abs hero-title">SAMPLE TEXT <span>FOR HEADLINE ONLY</span></h1>
  <p class="abs hero-copy">Lorem ipsum dolor sit amet, consectetur adipiscing elit. Curabitur lacinia pretium risus ac euismod. Aliquam auctor convallis mattis. lacinia pretium risus ac euismod. Aliquam auctor convallis mattis.</p>
  <div class="abs btn hero-btn">MAKE AN ENQUIRY</div>
  <div class="abs hero-dots"><i></i><i></i><i></i><i></i></div>
</section>

<section>
  <h2 class="abs welcome-title"><span>WELCOME TO</span> LANTERN PATHWAY</h2>
  <div class="abs welcome-rule"></div>
  <div class="abs welcome-copy">
    <p>Lantern Pathway is part of the Kestrelmoor Communication Group of Companies, who are providing speech language therapy, occupational therapy and educational therapy services to both the Singapore and the international school community.</p>
    <p>Lantern Pathway aims to work in an integrated manner, respecting the work of the respective professionals involved and collaborating effectively.</p>
  </div>
</section>

<section>
  <div class="abs services-band"></div>

  <article class="abs service-card" style="left:113px;width:276px">
    <h3 class="service-title"><span>Service</span> Name here</h3>
    <p class="service-text">Train shadows with a strong focus on equipping them with dynamic, clinical skills.</p>
    <div class="btn service-btn">READ MORE</div>
  </article>
  <div class="abs service-ring" style="left:140px">
    <svg width="196" height="196" role="img" aria-label="Photo of a therapist working with a child at a desk"><rect width="196" height="196" fill="#cfd9e2"/></svg>
  </div>

  <article class="abs service-card" style="left:464px;width:273px">
    <h3 class="service-title"><span>Service</span> Name here</h3>
    <p class="service-text">Provide families with well-trained Shadows who are mentored by Speech Language Pathologists and Professional Therapists to carry out shadow support.</p>
    <div class="btn service-btn">READ MORE</div>
  </article>
  <div class="abs service-ring" style="left:486px">
    <svg width="196" height="196" role="img" aria-label="Photo of children on a colourful classroom mat"><rect width="196" height="196" fill="#5a6f7d"/></svg>
  </div>

  <article class="abs service-card" style="left:809px;width:278px">
    <h3 class="service-title"><span>Service</span> Name here</h3>
    <p class="service-text">Work with educational professionals (Educational Psychologists) to provide an effective solution to the learning needs of a student.</p>
    <div class="btn service-btn">READ MORE</div>
  </article>
  <div class="abs service-ring" style="left:833px">
    <svg width="196" height="196" role="img" aria-label="Group photo of the professional team"><rect width="196" height="196" fill="#4a4a4e"/></svg>
  </div>
</section>

<section>
  <div class="abs support-band" role="img" aria-label="Faint red-tinted photo of a clinician in the background"></div>
  <h2 class="abs support-title">WHAT IS SHADOW SUPPORT?</h2>
  <div class="abs support-rule"></div>
  <p class="abs support-copy">A shadow support is para-professional who can help a struggling student to integrate and learn in their school environment. At different points in a student's life, there may be a need for a para-professional who could step in to help make a difference. Students who need shadows are those who:</p>
  <ul class="abs support-list">
    <li><svg width="12" height="12" viewBox="0 0 12 12"><path d="M0 6H10M6 2L10 6L6 10" stroke="#fff" stroke-width="1.8" fill="none"/></svg>Have difficulties in integrating learning in classroom</li>
    <li><svg width="12" height="12" viewBox="0 0 12 12"><path d="M0 6H10M6 2L10 6L6 10" stroke="#fff" stroke-width="1.8" fill="none"/></svg>Have social challenges and find it difficult to connect with peers</li>
    <li><svg width="12" height="12" viewBox="0 0 12 12"><path d="M0 6H10M6 2L10 6L6 10" stroke="#fff" stroke-width="1.8" fill="none"/></svg>Have difficulties in understanding instructions</li>
  </ul>
  <p class="abs support-goal">A central goal of the shadow support would be to help the student achieve independence in their learning journey eventually.</p>
  <div class="abs support-foot"></div>
</section>

<section>
  <div class="abs info"></div>
  <div class="abs info-col" style="left:162px;width:436px">
    <h3>What are its Advantages?</h3>
    <p>A fully trained shadow support is an asset to the student who otherwise would have trouble fitting in and adapting to the mainstream school environment.</p>
    <p>Additionally, working closely with the therapist at the centre would mean that the shadow is equipped with the skills necessary to not just adapt, but truly learn.</p>
    <h3>How do I know if my child needs shadowing</h3>
    <p>A consultation with our Speech Language Pathologist, along with an assessment by an Educational Psychologist would provide us with an indication of whether the child requires shadowing.</p>
  </div>
  <div class="abs info-col" style="left:667px;width:437px">
    <h3>How You Can Collaborate With Us <small>(For Referrers)</small></h3>
    <p class="tight">Shadow Support will participate in a collaborative working relationship with the professionals working with each student to facilitate progress</p>
    <p class="tight">Goals set out by professionals will be supported by the Shadow Support</p>
    <p class="tight">Frequent feedback and updates will be provided by the Shadow Support so that goals can remain relevant and up to date</p>
    <div class="btn info-btn">LEARN MORE</div>
  </div>
</section>

<footer>
  <div class="abs footer"></div>
  <h4 class="abs footer-head" style="left:114px">Navigation</h4>
  <h4 class="abs footer-head" style="left:329px">Useful Information</h4>
  <h4 class="abs footer-head" style="left:620px">Interact with us</h4>
  <h4 class="abs footer-head" style="left:881px">Newsletter</h4>
  <div class="abs footer-rule"></div>
  <ul class="abs footer-list" style="left:122px">
    <li>HOME</li><li>ABOUT US</li><li>SERVICES</li><li>NEWS</li><li>REGISTER</li><li>CONTACT US</li>
  </ul>
  <ul class="abs footer-list" style="left:337px">
    <li>Sitemap</li><li>FAQ</li><li>Terms &amp; Conditions</li><li>Privacy Policy</li>
  </ul>
  <div class="abs social" aria-label="Social links"><i></i><i></i><i></i><i></i></div>
  <div class="abs email">your email</div>
  <div class="abs subscribe">SUBSCRIBE</div>
  <div class="abs copyright">Copyright 2013 · All rights reserved</div>
</footer>
</body>
</html>
```